Modern business card design for professional copywriter

I'd like a business card design that I can use to have my cards printed out by quillprint.com as a squared corners business card (see artwork and design guidelines here: https://help.quillprint.com/hc/en-gb/sections/200570950-QUILL-Product-Templates)

The design should be clean and modern and reflect the colours, tone and branding on my website: https://tessavorrin.com.au

Target Market(s)

Professionals, B2B small business owners

Industry/Entity Type

Business

Contact Information for Business Card

Tessa Vorrin
m: 0468 905 327
e: tessa@tessavorrin.com.au
w: tessavorrin.com.au

Font styles to use
Sans Serif

Requirements
Must have
• Tagline: "Smart copywriting for clever business people"
• Brand colours: fd8000, 009984, 666666 and black
Nice to have

```html
<!DOCTYPE html>
<html lang="en">
<head>
<meta charset="utf-8">
<title>Tessa Vorrin – Business Card</title>
<link href="https://fonts.googleapis.com/css2?family=Open+Sans:wght@400;600&display=swap" rel="stylesheet">
<style>
  :root {
    --brand-orange: #f5821f;
    --brand-teal: #159c84;
    --brand-grey: #666666;
    --card-white: #f7f7f7;
    --stage: #e6e3e0;
    --ink-light: #ffffff;
  }
  * { margin: 0; padding: 0; box-sizing: border-box; }
  html, body {
    width: 1200px;
    height: 900px;
    overflow: hidden;
    background: var(--stage);
    font-family: "Open Sans", Arial, sans-serif;
  }
  .canvas { position: relative; width: 1200px; height: 900px; }

  .card { position: absolute; overflow: hidden; }

  /* Front of card */
  .card--front {
    left: 78px; top: 34px; width: 587px; height: 363px;
    background: var(--brand-teal);
    color: var(--ink-light);
  }
  .card-front__accent {
    position: absolute; left: 0; top: 0; width: 250px; height: 100%;
    background: linear-gradient(100deg, var(--brand-orange) 70%, #d9872e 100%);
  }
  .card-front__name {
    position: absolute; right: 34px; top: 36px;
    font-size: 22px; font-weight: 400; letter-spacing: 0.5px;
    text-transform: uppercase;
  }
  .contact-list {
    position: absolute; right: 34px; top: 172px;
    list-style: none; text-align: right;
    font-size: 15px; line-height: 21px;
  }
  .contact-list__item { display: flex; justify-content: flex-end; align-items: center; gap: 6px; }
  .contact-list__icon { width: 12px; height: 12px; flex: none; }
  .card-front__tagline {
    position: absolute; right: 36px; top: 268px;
    text-align: right; text-transform: uppercase;
    font-size: 16.5px; line-height: 21.5px; letter-spacing: 0.9px;
  }

  /* Back of card */
  .card--back {
    left: 388px; top: 505px; width: 567px; height: 352px;
    background: var(--card-white);
    display: flex; align-items: center; justify-content: center; gap: 12px;
  }
  .brand-dot { width: 18px; height: 18px; border-radius: 50%; background: var(--brand-orange); }
  .brand-name {
    font-size: 44px; font-weight: 600; color: var(--brand-teal); letter-spacing: -0.5px;
  }
</style>
</head>
<body>
<main class="canvas">

  <section class="card card--front" aria-label="Business card front">
    <div class="card-front__accent" role="img" aria-label="Large orange brand decoration sweeping across the left of the card"></div>
    <h1 class="card-front__name">Tessa Vorrin</h1>
    <ul class="contact-list">
      <li class="contact-list__item">0468 905 327
        <svg class="contact-list__icon" viewBox="0 0 12 12" aria-hidden="true"><rect x="3" y="0.5" width="6" height="11" rx="1" fill="none" stroke="#fff" stroke-width="1.2"/><rect x="4.3" y="2" width="3.4" height="6.5" fill="#fff"/></svg>
      </li>
      <li class="contact-list__item">tessa@tessavorrin.com.au
        <svg class="contact-list__icon" viewBox="0 0 12 12" aria-hidden="true"><rect x="0.5" y="2.5" width="11" height="7" fill="#fff"/><path d="M0.5 2.5 L6 6.5 L11.5 2.5" fill="none" stroke="#159c84" stroke-width="1"/></svg>
      </li>
      <li class="contact-list__item">tessavorrin.com.au
        <svg class="contact-list__icon" viewBox="0 0 12 12" aria-hidden="true"><circle cx="6" cy="6" r="5.5" fill="#fff"/><path d="M3 4 Q5 3 6 5 Q5 7 7 8 M8 3 Q9 5 10 5" fill="none" stroke="#159c84" stroke-width="1"/></svg>
      </li>
    </ul>
    <p class="card-front__tagline">Smart copywriting<br>for clever<br>business people</p>
  </section>

  <section class="card card--back" aria-label="Business card back">
    <span class="brand-dot" aria-hidden="true"></span>
    <span class="brand-name">Tessa Vorrin</span>
  </section>

</main>
</body>
</html>
```